1876 Basins & Spouts Business Card

I'm wanting to get a business card designed. Our business is 1876 Basins & Spouts
Details for the card:

1876 Basins & Spouts
Name: Harold Vesk
Email: harold@1876basinsandspouts.com.au
Website: www.1876basinsandspouts.com.au
Mobile: 0438 260 947
Phone: 02 7481 3926

Font of Basins & Spouts is called Snell Roundhand. Not sue what font logo text is.

I'm thinking two sided but it doesn't have to be.

```html
<!DOCTYPE html>
<html lang="en">
<head>
<meta charset="utf-8">
<title>1876 Basins &amp; Spouts – Business Card</title>
<link href="https://fonts.googleapis.com/css2?family=Pinyon+Script&family=Open+Sans:wght@400;600&display=swap" rel="stylesheet">
<style>
  :root {
    --backdrop: #2b2b2b;
    --card-dark: #1c1c1c;
    --card-light: #ffffff;
    --ink-light: #ffffff;
    --ink-dark: #111111;
    --rule: #333333;
  }
  * { box-sizing: border-box; margin: 0; padding: 0; }
  html, body {
    width: 1200px; height: 900px; overflow: hidden;
    background: var(--backdrop);
  }
  .sheet { position: relative; width: 1200px; height: 900px; }
  .card {
    position: absolute; left: 250px; width: 700px; height: 400px;
    box-shadow: 0 10px 30px rgba(0,0,0,.45);
  }
  .card--front { top: 30px; background: var(--card-dark); color: var(--ink-light); }
  .card--back { top: 470px; background: var(--card-light); color: var(--ink-dark); }

  .brand-mark {
    position: absolute;
    font-family: "Pinyon Script", cursive;
    font-size: 64px; line-height: 1;
  }
  .card--front .brand-mark { left: 75px; top: 165px; color: var(--ink-light); }
  .card--back .brand-mark { left: 100px; top: 165px; color: var(--ink-dark); }

  .brand-name {
    position: absolute; left: 265px; top: 118px;
    font-family: "Pinyon Script", cursive;
    font-size: 62px; font-weight: 400; line-height: 1.1;
    white-space: nowrap;
  }
  .tagline {
    position: absolute; left: 270px; top: 202px;
    font-family: "Open Sans", sans-serif;
    font-size: 15px; letter-spacing: .4px; white-space: nowrap;
  }

  .divider {
    position: absolute; left: 330px; top: 95px;
    width: 1px; height: 215px; background: var(--rule);
  }
  .contact { position: absolute; left: 370px; top: 95px; }
  .contact__name {
    font-family: "Pinyon Script", cursive;
    font-size: 44px; font-weight: 400; line-height: 1.1; margin-bottom: 14px;
  }
  .contact__list { list-style: none; }
  .contact__item {
    display: flex; align-items: center; gap: 12px;
    font-family: "Open Sans", sans-serif; font-size: 15px;
    height: 28px; white-space: nowrap;
  }
  .contact__icon { width: 14px; height: 14px; flex: none; }
</style>
</head>
<body>
<main class="sheet">
  <section class="card card--front" aria-label="Card front">
    <div class="brand-mark">1876</div>
    <h1 class="brand-name">Basins &amp; Spouts</h1>
    <p class="tagline">Pairing enduring elegance with everyday usefulness</p>
  </section>

  <section class="card card--back" aria-label="Card back">
    <div class="brand-mark">1876</div>
    <div class="divider"></div>
    <div class="contact">
      <h2 class="contact__name">Harold Vesk</h2>
      <ul class="contact__list">
        <li class="contact__item">
          <svg class="contact__icon" viewBox="0 0 14 14" aria-hidden="true"><rect x="3" y="0.5" width="8" height="13" rx="1.2" fill="none" stroke="#111" stroke-width="1.3"/><rect x="4.5" y="2.5" width="5" height="6" fill="#111"/></svg>
          0438 260 947
        </li>
        <li class="contact__item">
          <svg class="contact__icon" viewBox="0 0 14 14" aria-hidden="true"><path d="M3 1l2.5 0 1 3-1.5 1.2c.8 1.7 2 2.9 3.8 3.8L10 7.5l3 1v2.5c0 1-1 1.8-2 1.6C6 12 2 8 1.4 3 1.2 2 2 1 3 1z" fill="#111"/></svg>
          02 7481 3926
        </li>
        <li class="contact__item">
          <svg class="contact__icon" viewBox="0 0 14 14" aria-hidden="true"><rect x="0.5" y="2.5" width="13" height="9" fill="#111"/><path d="M0.5 2.5L7 8l6.5-5.5" fill="none" stroke="#fff" stroke-width="1"/></svg>
          harold@1876basinsandspouts.com.au
        </li>
        <li class="contact__item">
          <svg class="contact__icon" viewBox="0 0 14 14" aria-hidden="true"><circle cx="7" cy="7" r="6" fill="none" stroke="#111" stroke-width="1.2"/><ellipse cx="7" cy="7" rx="2.6" ry="6" fill="none" stroke="#111" stroke-width="1"/><path d="M1 7h12M2 4h10M2 10h10" stroke="#111" stroke-width="1"/></svg>
          www.1876basinsandspouts.com.au
        </li>
      </ul>
    </div>
  </section>
</main>
</body>
</html>
```